New Business Card Design Project

Use the flyer uploaded and website www.brightoakbuilders.com for inspiration.
List Our Services on Backside of business cards
Marcus Delling
Harborline Builders Inc.
Licensed General Contractors
858-471-6093

Contact Information for Business Card

Use the flyer uploaded and website www.brightoakbuilders.com for inspiration. List Our Services on Backside of business cards Marcus Delling Harborline Builders Inc. Licensed General Contractors 858-471-6093

```html
<!DOCTYPE html>
<html lang="en">
<head>
<meta charset="utf-8">
<title>Harborline Builders — Business Card</title>
<link href="https://fonts.googleapis.com/css2?family=Roboto:wght@400;500;700;900&display=swap" rel="stylesheet">
<style>
  :root{
    --stage:#222222;
    --card-light:#ffffff;
    --card-dark:#1b1b1b;
    --ink:#1a1a1a;
    --paper-text:#f2f2f2;
    --accent-red:#e3202a;
    --accent-blue:#4a7fd6;
    --rule:#2a2a2a;
  }
  *{box-sizing:border-box;margin:0;padding:0}
  html,body{width:1200px;height:780px;overflow:hidden;background:var(--stage)}
  body{font-family:"Roboto",Arial,sans-serif;display:flex;align-items:center;justify-content:center;gap:40px}
  .card{width:540px;height:310px;position:relative;border-radius:3px;overflow:hidden;box-shadow:0 14px 30px rgba(0,0,0,.45)}

  /* Front */
  .card--front{background:var(--card-light);color:var(--ink)}
  .front__brand{position:absolute;left:40px;top:78px;width:210px;text-align:center}
  .brand-name{font-weight:400;text-transform:uppercase;letter-spacing:3px;font-size:19px;line-height:1.3}
  .front__company{position:absolute;left:40px;bottom:36px;width:210px;text-align:center;font-size:13px}
  .front__divider{position:absolute;left:270px;top:70px;width:1px;height:190px;background:var(--rule)}
  .front__details{position:absolute;left:296px;top:86px}
  .person-name{color:var(--accent-red);font-weight:900;font-size:27px;text-transform:uppercase;letter-spacing:.5px;line-height:1}
  .person-title{font-size:13.5px;margin:6px 0 14px}
  .contact{list-style:none;font-size:13px}
  .contact li{display:flex;align-items:center;gap:8px;margin-bottom:6px}
  .contact svg{width:13px;height:13px;flex:none}

  /* Back */
  .card--back{background:var(--card-dark);color:var(--paper-text);text-align:center}
  .back__brand{margin-top:62px}
  .back__brand .brand-name{font-size:22px;color:var(--paper-text)}
  .guarantee{color:var(--accent-red);font-weight:900;font-size:12.5px;text-transform:uppercase;margin-top:28px;letter-spacing:.3px}
  .specialty{color:var(--accent-blue);font-weight:900;font-size:12px;text-transform:uppercase;margin-top:4px}
  .services{list-style:none;font-size:11px;line-height:1.55;margin-top:8px;padding:0 26px;display:flex;flex-wrap:wrap;justify-content:center;column-gap:8px}
  .services li{display:flex;align-items:center;gap:3px}
  .services svg{width:9px;height:9px;flex:none}
</style>
</head>
<body>

<section class="card card--front" aria-label="Business card front">
  <div class="front__brand"><p class="brand-name">Harborline Builders</p></div>
  <p class="front__company">Harborline Builders Inc.</p>
  <span class="front__divider"></span>
  <div class="front__details">
    <h1 class="person-name">Marcus Delling</h1>
    <p class="person-title">Licensed General Contractors</p>
    <ul class="contact">
      <li>
        <svg viewBox="0 0 16 16" aria-hidden="true"><path fill="#e3202a" d="M3.6 1.5l2.2 2.6-1.2 1.6c.9 2 2.6 3.7 4.6 4.6l1.6-1.2 2.6 2.2-1.3 2.2C6.8 13.3 2.7 9.2 1.4 3.9z"/></svg>
        858-471-6093
      </li>
      <li>
        <svg viewBox="0 0 16 16" aria-hidden="true"><rect x="1" y="3" width="14" height="10" rx="1.5" fill="#e3202a"/><path d="M1.5 4l6.5 5 6.5-5" stroke="#fff" stroke-width="1.3" fill="none"/></svg>
        info@brightoakbuilders.com
      </li>
      <li>
        <svg viewBox="0 0 16 16" aria-hidden="true"><circle cx="8" cy="8" r="7" fill="#e3202a"/><path d="M1 8h14M8 1c-3 3.5-3 10.5 0 14M8 1c3 3.5 3 10.5 0 14" stroke="#fff" stroke-width="1" fill="none"/></svg>
        www.brightoakbuilders.com
      </li>
    </ul>
  </div>
</section>

<section class="card card--back" aria-label="Business card back">
  <div class="back__brand"><p class="brand-name">Harborline Builders</p></div>
  <p class="guarantee">Our services are 100% guaranteed</p>
  <p class="specialty">Specializing in:</p>
  <ul class="services">
    <li><svg viewBox="0 0 10 10"><circle cx="5" cy="5" r="4.3" fill="none" stroke="#e3202a"/><path d="M3 5.2l1.5 1.4L7.2 3.6" stroke="#e3202a" fill="none" stroke-width="1.2"/></svg>Remodel: Kitchen &amp; Bath</li>
    <li><svg viewBox="0 0 10 10"><circle cx="5" cy="5" r="4.3" fill="none" stroke="#e3202a"/><path d="M3 5.2l1.5 1.4L7.2 3.6" stroke="#e3202a" fill="none" stroke-width="1.2"/></svg>Painting: Interior &amp; Exterior</li>
    <li><svg viewBox="0 0 10 10"><circle cx="5" cy="5" r="4.3" fill="none" stroke="#e3202a"/><path d="M3 5.2l1.5 1.4L7.2 3.6" stroke="#e3202a" fill="none" stroke-width="1.2"/></svg>Flooring: Carpet, Vinyl, Wood</li>
    <li><svg viewBox="0 0 10 10"><circle cx="5" cy="5" r="4.3" fill="none" stroke="#e3202a"/><path d="M3 5.2l1.5 1.4L7.2 3.6" stroke="#e3202a" fill="none" stroke-width="1.2"/></svg>Window &amp; Door Replacement</li>
    <li><svg viewBox="0 0 10 10"><circle cx="5" cy="5" r="4.3" fill="none" stroke="#e3202a"/><path d="M3 5.2l1.5 1.4L7.2 3.6" stroke="#e3202a" fill="none" stroke-width="1.2"/></svg>Plumbing: Repairs &amp; Upgrades</li>
    <li><svg viewBox="0 0 10 10"><circle cx="5" cy="5" r="4.3" fill="none" stroke="#e3202a"/><path d="M3 5.2l1.5 1.4L7.2 3.6" stroke="#e3202a" fill="none" stroke-width="1.2"/></svg>Energy-Efficient Upgrades</li>
    <li><svg viewBox="0 0 10 10"><circle cx="5" cy="5" r="4.3" fill="none" stroke="#e3202a"/><path d="M3 5.2l1.5 1.4L7.2 3.6" stroke="#e3202a" fill="none" stroke-width="1.2"/></svg>Deck &amp; Patio Construction</li>
    <li><svg viewBox="0 0 10 10"><circle cx="5" cy="5" r="4.3" fill="none" stroke="#e3202a"/><path d="M3 5.2l1.5 1.4L7.2 3.6" stroke="#e3202a" fill="none" stroke-width="1.2"/></svg>Water &amp; Mold Damage</li>
    <li><svg viewBox="0 0 10 10"><circle cx="5" cy="5" r="4.3" fill="none" stroke="#e3202a"/><path d="M3 5.2l1.5 1.4L7.2 3.6" stroke="#e3202a" fill="none" stroke-width="1.2"/></svg>Garage Renovation</li>
  </ul>
</section>

</body>
</html>
```